Innovative modern square business card design for law firm

We require a highly modern innovative styled SQUARE business card (double sided) design & layout for our law firm (PLUS an accompanying letterhead design), which specialises mainly in criminal defence. However included somewhere in the design should display the icons representative of all four different areas of law in which the firm offers services. Each card to display the name of the lawyer, job title, telephone number, switchboard, email, web address, facebook & twitter details + physical address. Attached is the main logo + icons of each of the other departments to be included as well as the firms main overhaul icon (all of which can be used or blended into the overall in some way.(note. high res versions of these icons can be provided if required by the design))

Industry/Entity Type

Law Firm

```html
<!DOCTYPE html>
<html lang="en">
<head>
<meta charset="utf-8">
<title>Harlow Defence – Business Card</title>
<link href="https://fonts.googleapis.com/css2?family=Lato:wght@400;700;900&display=swap" rel="stylesheet">
<style>
  :root {
    --navy: #123a57;
    --navy-dark: #0d2c44;
    --ink: #163a55;
    --card: #ffffff;
    --stage: #e6e9ec;
    --dept-green: #1f3b1f;
    --dept-orange: #e07a1c;
    --dept-red: #c4161c;
    --dept-blue: #1f2f8f;
  }
  * { box-sizing: border-box; margin: 0; padding: 0; }
  html, body { width: 1200px; height: 900px; overflow: hidden; }
  body {
    background: var(--stage);
    font-family: "Lato", Arial, sans-serif;
    color: var(--ink);
    position: relative;
  }
  .card {
    position: absolute;
    background: var(--card);
    box-shadow: 0 8px 24px rgba(0,0,0,.18);
    overflow: hidden;
  }
  .card-bands { position: absolute; inset: 0; }

  /* Back side */
  .card-back { left: 40px; top: 40px; width: 560px; height: 320px; }
  .card-back .brand { position: absolute; left: 0; right: 0; top: 80px; text-align: center; }
  .brand-mark {
    display: inline-block; width: 44px; height: 44px; background: var(--navy);
    border-radius: 4px; vertical-align: middle; margin-right: 12px;
  }
  .brand-name {
    display: inline-block; vertical-align: middle;
    font-weight: 700; font-size: 34px; letter-spacing: 1px; color: var(--ink);
  }
  .brand-phone { display: block; font-weight: 700; font-size: 12px; margin-top: 10px; }
  .tagline {
    position: absolute; left: 0; right: 0; top: 210px; text-align: center;
    font-size: 15px; letter-spacing: 5px; text-transform: uppercase;
  }

  /* Front side */
  .card-front { left: 400px; top: 420px; width: 760px; height: 434px; }
  .card-front .brand { position: absolute; left: 0; right: 0; top: 62px; text-align: center; }
  .card-front .brand-phone { margin-top: 8px; }

  .person { position: absolute; right: 420px; top: 178px; text-align: right; }
  .person-name { font-weight: 900; font-size: 24px; line-height: 1; }
  .person-role { font-weight: 700; font-size: 17px; margin-top: 2px; }

  .departments { position: absolute; left: 190px; top: 250px; display: flex; gap: 14px; }
  .department {
    width: 36px; height: 32px; border-radius: 4px;
  }
  .department.green { background: var(--dept-green); }
  .department.orange { background: var(--dept-orange); }
  .department.red { background: var(--dept-red); }
  .department.blue { background: var(--dept-blue); }

  .social { position: absolute; right: 420px; top: 298px; text-align: right; }
  .social-line { font-weight: 700; font-size: 16px; line-height: 30px; }
  .social-dot {
    display: inline-block; width: 14px; height: 14px; border-radius: 50%;
    background: var(--navy); vertical-align: -1px; margin-right: 8px;
  }

  .divider {
    position: absolute; left: 364px; top: 172px; width: 3px; height: 170px;
    background: linear-gradient(to bottom, rgba(18,58,87,.1), var(--navy) 40%, rgba(18,58,87,.1));
  }

  .contact { position: absolute; left: 392px; top: 170px; }
  .address { font-weight: 900; font-size: 15px; line-height: 19px; text-transform: uppercase; }
  .contact-line { display: flex; align-items: center; font-weight: 700; font-size: 16px; margin-top: 12px; }
  .contact-line svg { width: 18px; height: 18px; margin-right: 12px; fill: var(--navy); }
  .website { font-weight: 900; font-size: 19px; margin-top: 16px; }
</style>
</head>
<body>

<section class="card card-back" aria-label="Business card, back">
  <svg class="card-bands" viewBox="0 0 560 320" preserveAspectRatio="none">
    <path d="M0,320 V300 H380 Q410,300 425,270 H560 V320 Z" fill="var(--navy)"/>
    <path d="M560,0 V40 Q545,40 545,0 Z" fill="var(--navy)"/>
  </svg>
  <div class="brand">
    <span class="brand-mark"></span><span class="brand-name">HARLOW DEFENCE</span>
    <span class="brand-phone">0800 555 0199 (24hrs)</span>
  </div>
  <p class="tagline">Specialist legal advice to trust</p>
</section>

<section class="card card-front" aria-label="Business card, front">
  <svg class="card-bands" viewBox="0 0 760 434" preserveAspectRatio="none">
    <path d="M150,0 H760 V18 H205 Q172,18 150,0 Z" fill="var(--navy)"/>
    <path d="M0,434 V406 H560 Q600,406 618,382 H760 V434 Z" fill="var(--navy)"/>
  </svg>

  <div class="brand">
    <span class="brand-mark"></span><span class="brand-name">HARLOW DEFENCE</span>
    <span class="brand-phone">0800 555 0199 (24hrs)</span>
  </div>

  <div class="person">
    <p class="person-name">YOUR NAME</p>
    <p class="person-role">Designation</p>
  </div>

  <div class="departments" aria-label="Practice areas">
    <span class="department green"></span>
    <span class="department orange"></span>
    <span class="department red"></span>
    <span class="department blue"></span>
  </div>

  <div class="social">
    <p class="social-line"><span class="social-dot"></span>/DefenceLawHelp</p>
    <p class="social-line"><span class="social-dot"></span>/defencesolicitorslondon</p>
  </div>

  <div class="divider"></div>

  <div class="contact">
    <p class="address">12 Example Row, SE1 0AA,<br>London, United Kingdom</p>
    <p class="contact-line">
      <svg viewBox="0 0 24 24"><rect x="2" y="10" width="20" height="11" rx="2"/><path d="M2 9c0-4 20-4 20 0v1H2z"/></svg>
      +44 20 7946 0123
    </p>
    <p class="contact-line">
      <svg viewBox="0 0 24 24"><path d="M6.6 10.8a15 15 0 0 0 6.6 6.6l2.2-2.2a1 1 0 0 1 1-.25 11.4 11.4 0 0 0 3.6.57 1 1 0 0 1 1 1V20a1 1 0 0 1-1 1A17 17 0 0 1 3 4a1 1 0 0 1 1-1h3.5a1 1 0 0 1 1 1c0 1.25.2 2.45.57 3.57a1 1 0 0 1-.25 1z"/></svg>
      020 7946 04567
    </p>
    <p class="contact-line">
      <svg viewBox="0 0 24 24"><rect x="2" y="5" width="20" height="14" rx="1"/><path d="M3 6l9 7 9-7" fill="none" stroke="#fff" stroke-width="1.8"/></svg>
      anna@harlowdefence.co.uk
    </p>
    <p class="website">www.harlowdefence.co.uk</p>
  </div>
</section>

</body>
</html>
```